Spring Detox sale graphics for social media

You MUST read the Brief in the WORD document and follow the instructions there. I want to create 10 social media graphics (new Instagram size 4:5 (1080 x 1350 pixels) focusing on our Mother’s Day Spring Detox Sale graphics, using any of the pics attached. Use the attached pics, NO RANDOM STOCK PHOTOGRAPHY. For the color scheme of the graphics, they should all be complementary to the product colors or feel like Spring time.

Target Market(s)

primarily women

Requirements
Must have
• the photos and text attached

```html
<!DOCTYPE html>
<html lang="en">
<head>
<meta charset="utf-8">
<title>Spring Detox Sale – Social Graphics</title>
<link rel="stylesheet" href="https://fonts.googleapis.com/css2?family=Pinyon+Script&family=Poppins:wght@600;800;900&display=swap">
<style>
  :root {
    --stage: #9e9e9e;
    --paper: #f1eff0;
    --white: #ffffff;
    --pink: #e2609f;
    --pink-soft: #f3b8d3;
    --purple: #a66fb0;
    --plum: #9a5aa8;
    --ink: #1d1d1d;
    --script: "Pinyon Script", cursive;
    --sans: "Poppins", sans-serif;
  }
  * { margin: 0; padding: 0; box-sizing: border-box; }
  html, body { width: 1200px; height: 384px; overflow: hidden; background: var(--stage); }
  .stage { position: relative; width: 1200px; height: 384px; }
  .post {
    position: absolute; top: 30px; width: 260px; height: 323px; overflow: hidden;
    background: var(--paper); box-shadow: 0 2px 4px rgba(0,0,0,.25);
  }
  .post--one { left: 32px; background: linear-gradient(135deg, #f6c6dc 0%, var(--paper) 30%, var(--paper) 70%, #f6c6dc 100%); }
  .post--two { left: 325px; background: linear-gradient(135deg, #ef9cc4, #f7d3e4 50%, #ef9cc4); }
  .post--three { left: 616px; background: linear-gradient(180deg, #f5c9dd 0%, var(--paper) 35%); }
  .post--four { left: 908px; background: var(--white); }

  .line { position: absolute; text-align: center; left: 0; right: 0; line-height: 1; white-space: nowrap; }
  .script { font-family: var(--script); color: var(--pink); }
  .heavy { font-family: var(--sans); font-weight: 800; letter-spacing: .5px; }
  .dark { color: var(--ink); }
  .gradient {
    background: linear-gradient(180deg, var(--pink), var(--purple));
    -webkit-background-clip: text; background-clip: text; color: transparent;
  }
  .offer {
    position: absolute; border: 2px solid var(--pink); padding: 2px;
  }
  .offer span {
    display: flex; align-items: center; justify-content: center; height: 100%;
    background: var(--pink); color: var(--white);
    font-family: var(--sans); font-weight: 800;
  }
  .rule { position: absolute; background: var(--purple); }
  .rule--pink { background: var(--pink); }
  .art { position: absolute; }

  /* panel two */
  .frame-inner { position: absolute; left: 6px; top: 8px; width: 247px; height: 307px; background: var(--white); border: 1px solid var(--pink); }
  .label-box { position: absolute; left: 73px; top: 46px; width: 114px; height: 40px; border: 1.5px solid var(--pink); background: var(--white); display: flex; align-items: center; justify-content: center; }

  /* panel three */
  .band { position: absolute; top: 0; bottom: 0; }
</style>
</head>
<body>
<main class="stage">

  <!-- Post 1 -->
  <section class="post post--one">
    <div class="art" role="img" aria-label="Pink roses cluster" style="left:0;top:0;width:100px;height:50px;background:radial-gradient(ellipse at 30% 40%, #f4a9c3, rgba(246,198,220,0) 70%);"></div>
    <div class="art" role="img" aria-label="Pink roses cluster" style="right:0;bottom:0;width:100px;height:50px;background:radial-gradient(ellipse at 65% 60%, #f4a9c3, rgba(246,198,220,0) 70%);"></div>
    <div class="rule" style="left:102px;top:6px;width:150px;height:1.5px;"></div>
    <div class="rule" style="left:120px;top:12px;width:132px;height:1px;"></div>
    <div class="rule" style="left:251px;top:6px;width:1.5px;height:200px;"></div>
    <div class="rule" style="left:245px;top:12px;width:1px;height:150px;"></div>
    <div class="rule" style="left:8px;top:125px;width:1.5px;height:192px;"></div>
    <div class="rule" style="left:14px;top:165px;width:1px;height:150px;"></div>
    <div class="rule" style="left:8px;top:316px;width:140px;height:1.5px;"></div>
    <div class="rule" style="left:14px;top:310px;width:110px;height:1px;"></div>

    <p class="line script" style="top:62px;font-size:21px;">Mother’s Day</p>
    <p class="line heavy dark" style="top:88px;font-size:29px;">SPRING</p>
    <p class="line heavy dark" style="top:120px;font-size:29px;">DETOX</p>
    <p class="line heavy gradient" style="top:155px;font-size:54px;">SALE!</p>
    <div class="offer" style="left:78px;top:216px;width:105px;height:28px;"><span style="font-size:17px;">25% OFF</span></div>
    <p class="line heavy dark" style="top:251px;font-size:18px;">EVERYTHING!</p>
  </section>

  <!-- Post 2 -->
  <section class="post post--two">
    <div class="frame-inner"></div>
    <div class="art" role="img" aria-label="Soft white flower backdrop" style="left:7px;top:170px;width:245px;height:144px;background:radial-gradient(ellipse at 45% 70%, #efe6e0, rgba(255,255,255,0) 70%);"></div>
    <p class="line script" style="top:18px;font-size:19px;">Mother’s Day Sale</p>
    <div class="label-box"><span class="heavy dark" style="font-size:27px;line-height:1;">DETOX</span></div>
    <p class="line heavy gradient" style="top:93px;font-size:33px;">THIS</p>
    <p class="line heavy gradient" style="top:131px;font-size:33px;">SPRING</p>
    <p class="line heavy dark" style="top:170px;font-size:33px;">SHINE THIS</p>
    <p class="line heavy dark" style="top:207px;font-size:33px;">SUMMER</p>
    <div class="offer" style="left:76px;top:250px;width:107px;height:28px;"><span style="font-size:17px;">25% OFF</span></div>
    <p class="line heavy dark" style="top:286px;font-size:18px;">EVERYTHING!</p>
  </section>

  <!-- Post 3 -->
  <section class="post post--three">
    <div class="band" style="left:165px;width:5px;background:var(--purple);"></div>
    <div class="band" style="left:177px;width:83px;background:linear-gradient(180deg, var(--purple), #cf6fb0);"></div>
    <div class="art" role="img" aria-label="Smiling woman presenting supplement bottles on a wooden table" style="left:92px;top:82px;width:168px;height:241px;background:linear-gradient(180deg, rgba(240,235,238,0) 0%, #efe9ec 55%, #e6dbd2 88%, #d8c2a4 100%);"></div>
    <div class="rule rule--pink" style="left:20px;top:11px;width:137px;height:1.5px;"></div>
    <div class="rule rule--pink" style="left:20px;top:11px;width:1.5px;height:27px;"></div>
    <div class="rule rule--pink" style="left:20px;top:247px;width:1.5px;height:25px;"></div>
    <div class="rule rule--pink" style="left:20px;top:272px;width:60px;height:1.5px;"></div>

    <p class="line script dark" style="left:15px;text-align:left;top:45px;font-size:19px;color:var(--ink);">Mother’s</p>
    <p class="line script dark" style="left:15px;text-align:left;top:66px;font-size:19px;color:var(--ink);">Day Sale</p>
    <p class="line heavy gradient" style="left:15px;text-align:left;top:91px;font-size:29px;">SPRING</p>
    <p class="line heavy gradient" style="left:15px;text-align:left;top:125px;font-size:29px;">DETOX</p>
    <p class="line heavy gradient" style="left:15px;text-align:left;top:158px;font-size:29px;">SALE</p>
    <div class="offer" style="left:16px;top:195px;width:83px;height:23px;"><span style="font-size:14px;">25% OFF</span></div>
    <p class="line heavy dark" style="left:15px;text-align:left;top:226px;font-size:11.5px;">EVERYTHING!</p>
  </section>

  <!-- Post 4 -->
  <section class="post post--four">
    <div class="art" style="left:0;top:190px;width:260px;height:70px;background:linear-gradient(180deg, rgba(255,255,255,0), #d98ac0);"></div>
    <div class="art" role="img" aria-label="Four supplement bottles in a row" style="left:14px;top:205px;width:232px;height:110px;background:linear-gradient(180deg, #f4eef1 0%, #ffffff 70%);border-radius:6px;opacity:.9;"></div>
    <div style="position:absolute;left:7px;top:7px;width:246px;height:309px;border:1px solid var(--pink);"></div>
    <p class="line" style="top:20px;font-family:var(--sans);font-weight:600;font-size:10px;color:var(--purple);letter-spacing:.5px;">ALL SUPPLEMENTS</p>
    <p class="line heavy gradient" style="top:37px;font-size:40px;">SPRING</p>
    <p class="line heavy gradient" style="top:79px;font-size:40px;">DETOX</p>
    <p class="line heavy gradient" style="top:120px;font-size:40px;">SALE!</p>
    <div class="offer" style="left:80px;top:165px;width:99px;height:26px;"><span style="font-size:16px;">25% OFF</span></div>
  </section>

</main>
</body>
</html>
```